Create a Dynamic Website for Roadhaven 41Ter!

Dear designers,
We have an exciting design opportunity for you on PixelBazaar. We are in need of a creative and professional website design for our company, Roadhaven 41Ter. Our current website is outdated and fails to convey the image we want to project. We are determined to revamp our online presence and create a website that truly represents who we are.
Roadhaven 41Ter is a versatile establishment offering a Velko Express, sandwich bar, restaurant, parking facilities, and meeting rooms. Each of these aspects deserves its own spotlight on our website. Therefore, we are seeking a WordPress-based website design that allows us to easily make changes, modify texts, and add new content as needed.
It is crucial that the design aligns seamlessly with our new branding and style. We invite you to explore our Instagram (@Roadhaven41ter) and Facebook (@Roadhaven) pages to gain an understanding of our branding and incorporate those elements into the design.
You can find our current website at www.guardedroadhaven.eu, but we want a new website that is vibrant, dynamic, and includes moving elements if possible. We believe this will enhance the user experience and keep visitors engaged for longer periods.
Key elements we would like to include in the new website design are as follows:
Clear presentation of all our services: Velko Express, sandwich bar, restaurant, parking facilities, and meeting rooms.
Easy navigation for visitors to find information effortlessly.
Engaging call-to-action buttons that encourage visitors to take specific actions, such as reserving a meeting room or placing an order.
A dedicated blog section where we can share news, events, and special offers.
Integration of a contact form and contact details for easy communication with our visitors.
Responsive design that works seamlessly across desktop and mobile devices.
We envision a modern and visually appealing website that leaves a lasting positive impression on visitors. We are interested in a design that incorporates creative visual elements and provides a user-friendly interface.
Thank you for your time, and we eagerly await your designs.
Best regards,

```html
<!DOCTYPE html>
<html lang="nl">
<head>
<meta charset="utf-8">
<title>Roadhaven 41Ter</title>
<link href="https://fonts.googleapis.com/css2?family=Audiowide&family=Outfit:wght@400;500;600;700&display=swap" rel="stylesheet">
<style>
:root{
  --red:#e31b37;
  --navy:#1b2364;
  --blue:#1a73c0;
  --ink:#222;
  --line:#bcd6ee;
  --map:#4a4d55;
}
*{box-sizing:border-box;margin:0;padding:0}
html,body{width:1200px;height:3402px;overflow:hidden}
body{position:relative;font-family:"Outfit",sans-serif;color:var(--ink);background:#fff}
.abs{position:absolute}
.display{font-family:"Audiowide",sans-serif}
.btn{position:absolute;display:flex;align-items:center;justify-content:center;color:#fff;font-size:13px;font-weight:500;border-radius:3px}
.btn-red{background:var(--red)}
.btn-blue{background:var(--blue)}
.btn-navy{background:var(--navy)}

/* header */
.contact-col{font-size:11.5px;line-height:19px}
.contact-col b{color:var(--red);font-weight:500}
.brand{left:520px;top:14px;width:160px;text-align:center;font-size:26px;font-weight:700;color:var(--navy);line-height:28px}
.follow{left:764px;top:32px;font-size:12px;color:var(--red);display:flex;align-items:center;gap:8px}
.dot-icon{width:21px;height:21px;border-radius:50%;background:var(--blue)}
.header-rule{left:55px;top:83px;width:1088px;height:1px;background:var(--red);opacity:.5}
.nav{top:97px;left:0;width:1200px;display:flex;font-size:12.5px;font-weight:500}
.nav span{position:absolute}
/* hero */
.hero{left:0;top:135px;width:1200px;height:479px;background:linear-gradient(160deg,#5d646b,#3a3f45 55%,#6b6e70)}
.hero-red{left:55px;top:279px;width:482px;height:95px;background:var(--red);color:#fff;font-size:68px;display:flex;align-items:center;padding-left:32px}
.hero-blue{left:537px;top:374px;width:606px;height:97px;background:var(--blue);color:#fff;font-size:68px;display:flex;align-items:center;padding-left:20px}
.dots{left:568px;top:577px;display:flex;gap:10px}
.dots i{width:12px;height:12px;border-radius:50%;background:#fff}
.dots i.on{background:var(--red)}
/* about */
.eyebrow{width:1200px;left:0;text-align:center;color:var(--red);font-size:18px;font-weight:500}
.section-title{width:1200px;left:0;text-align:center;color:var(--navy);font-size:29px}
.about-text{left:337px;top:758px;width:530px;text-align:center;font-size:12.3px;line-height:21.7px}
.photo{position:absolute}
/* services */
.services{left:0;top:1228px;width:1200px;height:617px;background:var(--navy)}
.card-title{color:#fff;font-size:23px}
.card-text{color:#fff;font-size:12px;line-height:21.5px;width:350px}
.arrow-btn{width:23px;height:21px;background:var(--red);display:flex;align-items:center;justify-content:center}
/* hours */
.hours{left:352px;top:1930px;font-size:17px;line-height:34.3px;color:var(--navy)}
.hours b{color:var(--red);font-family:"Audiowide",sans-serif;font-weight:400}
/* contact form */
.form-box{left:632px;top:1786px;width:511px;height:487px;background:var(--red);color:#fff}
.field{position:absolute;left:25px;width:460px;border:1px solid rgba(255,255,255,.8);font-size:12.5px;padding:10px 9px}
/* blog */
.post{position:absolute;left:108px;width:984px;height:266px;border:1px solid var(--line)}
.post-img{position:absolute;left:25px;top:19px;width:458px;height:227px}
.date{position:absolute;left:442px;top:93px;width:74px;height:74px;border-radius:50%;background:var(--blue);color:#fff;font-size:14px;font-weight:500;text-align:center;display:flex;align-items:center;justify-content:center;line-height:17px}
.post-title{position:absolute;left:533px;top:18px;width:420px;color:var(--navy);font-size:19.5px;line-height:25px}
.meta{position:absolute;left:533px;top:78px;display:flex;gap:22px;font-size:12px;align-items:center}
.meta span{display:flex;align-items:center;gap:6px}
.post-text{position:absolute;left:533px;top:113px;width:420px;font-size:12px;line-height:21.8px}
/* footer */
.map{left:0;top:3152px;width:1200px;height:211px;background:linear-gradient(135deg,#55585f,#3f4249 60%,#4d5058)}
.footer{left:0;top:3363px;width:1200px;height:39px;background:var(--blue);color:#fff;font-size:12px}
</style>
</head>
<body>

<!-- header -->
<div class="abs contact-col" style="left:55px;top:9px"><b>Restaurant:</b> 011 720 310<br><b>Broodjesbar:</b> 011 720 312<br><b>Velko Express:</b> 011 720 314</div>
<div class="abs contact-col" style="left:265px;top:9px;line-height:15.5px"><b>Address:</b> Havenlaan 27<br>3590 Meerbeek-Oost<br><span style="display:block;height:6px"></span><b>Email:</b> jobs@guardedroadhaven.eu</div>
<div class="abs brand">Roadhaven<br>41Ter</div>
<div class="abs follow">Volg Ons <span class="dot-icon"></span><span class="dot-icon"></span></div>
<div class="btn btn-red" style="left:973px;top:24px;width:171px;height:35px;font-size:12.5px">Boek Een Vergaderruimte</div>
<div class="abs header-rule"></div>
<nav class="abs nav">
  <span style="left:152px;color:var(--red)">Home</span>
  <span style="left:232px">Over Ons</span>
  <span style="left:332px">Velko Express</span>
  <span style="left:460px">Sandwich Bar</span>
  <span style="left:587px">Restaurant</span>
  <span style="left:704px">Parking Facilities</span>
  <span style="left:854px">Meeting Rooms</span>
  <span style="left:995px">Contact</span>
</nav>

<!-- hero -->
<div class="abs hero" role="img" aria-label="Luchtfoto van het terrein met loodsen, parking en silo's"></div>
<div class="abs hero-red display">EEN THUIS</div>
<div class="abs hero-blue display">VER VAN HUIS.</div>
<div class="abs dots"><i></i><i class="on"></i><i></i></div>

<!-- about -->
<div class="abs eyebrow" style="top:643px">Over Ons</div>
<div class="abs section-title display" style="top:672px">ZOVEEL MEER DAN EEN TRUCKSTOP.</div>
<div class="photo" style="left:0;top:748px;width:301px;height:439px;background:linear-gradient(170deg,#b8c6d2,#6f7f8c 60%,#3d4650)" role="img" aria-label="Gevel van het gebouw met naambord"></div>
<div class="abs about-text">In 2009 Ontstond Roadhaven41Ter Dankzij Vier Vennoten, Met Een Sterke Visie Rond Veiligheid En Comfort Voor Truckchauffeurs.Anno 2020 Zijn Het De Gebroeders Vandael Die Deze Visie Verder Zetten.<br>Transport Is Dan Ook Onmisbaar In Onze Huidige Maatschappij.<br>De Gebroeders Vandael, Zelf Ook Actief In De Transportwereld, Weten Waar De Pijnpunten Liggen In De Sector. Daarom Streven Zij Met Roadhaven41Ter Een Oplossing Te Bieden Op De Problematiek Rond Veiligheid, Comfort, Hygiëne, Parking En Degelijke Gezonde Maaltijden..<br><br>Dit Doen Ze Door: Verschillende Beveiligingssystemen Te Gebruiken, Verder Bieden Ze Een Restaurant, Een Velko-Express En Maar Liefst 7 Individuele, Ruime Douchecabines.<br><br>Maar Ook Voor Onze Buurtbewoners Staan Wij 7/7 Klaar.<br>Jong Of Oud, Fietser Of Wandelaar, Grote Of Kleine Groepen… Iedereen Is Bij Ons Welkom Om Gezellig Te Vertoeven In De Brasserie, De Veranda Of Op Ons Terras. Samen Kunnen Jullie Bij Ons Genieten Van Een Natje Of Een Droogje. Neem Gerust De Kinderen Mee Ook Aan Hun Wordt Gedacht. We Hebben Dan Ook Een Speelhoek En Bij Goed Weer Onze Buitenspeeltuin Met Springkasteel!</div>
<div class="btn btn-blue" style="left:514px;top:1143px;width:171px;height:34px">Bekijk Onze Tijdlijn</div>
<div class="photo" style="left:898px;top:748px;width:302px;height:439px;background:linear-gradient(160deg,#9fc4d8,#3f7d9c 45%,#7a5a3c)" role="img" aria-label="Terras onder een tent met gasten en slingers"></div>

<!-- services -->
<div class="abs services"></div>
<div class="abs section-title display" style="top:1251px;color:#fff">ONZE DIENSTEN</div>

<div class="photo" style="left:55px;top:1319px;width:349px;height:231px;background:linear-gradient(135deg,#3a4a5a,#8a6a4a 60%,#2b3440)" role="img" aria-label="Vrienden die proosten in het restaurant"></div>
<div class="abs card-title display" style="left:55px;top:1561px">Restaurant</div>
<div class="abs card-text" style="left:55px;top:1600px">Ons Restaurant Is Een Gezellige Warme Plek Om Te Vertoeven. Met Onze Uitgebreide Menukaart Is Er Voor Ieder Wat Wils.</div>
<div class="btn btn-red" style="left:55px;top:1679px;width:118px;height:34px">Lees Verder</div>

<div class="photo" style="left:425px;top:1319px;width:349px;height:231px;background:linear-gradient(135deg,#d8dcdf,#9aa3aa 60%,#5a6066)" role="img" aria-label="Vergadering in een lichte vergaderzaal"></div>
<div class="abs card-title display" style="left:425px;top:1561px">Vergaderzalen</div>
<div class="abs card-text" style="left:425px;top:1600px">Zoekt U Nog Een Vergaderzaal? Dan Is Roadhaven41Ter De Perfecte Locatie. Wij Beschikken Over 4 Vergaderruimte's Met Een Maximum Capaciteit Van 70p.</div>
<div class="btn btn-red" style="left:425px;top:1679px;width:118px;height:34px">Lees Verder</div>

<div class="photo" style="left:791px;top:1319px;width:349px;height:231px;background:linear-gradient(170deg,#d9dde0,#a8acad 55%,#c2bfb8)" role="img" aria-label="Auto aan de laadpalen op de parking"></div>
<div class="abs card-title display" style="left:791px;top:1561px">Parkeren</div>
<div class="abs card-text" style="left:791px;top:1600px">Voor Een Extra Beveiligde Parking Is Roadhaven Voorzien Van 2 Slagbomen ( In- En Uitrit) Deze Zijn Uigerust Waardoor Er Enkel Vrachtwagens Kunnen Binnenrijden</div>
<div class="btn btn-red" style="left:791px;top:1679px;width:118px;height:34px">Lees Verder</div>

<div class="abs arrow-btn" style="left:1088px;top:1732px"><svg width="12" height="10" viewBox="0 0 12 10"><path d="M6 1 2 5l4 4M10 1 6 5l4 4" fill="none" stroke="#fff" stroke-width="1.5"/></svg></div>
<div class="abs arrow-btn" style="left:1120px;top:1732px"><svg width="12" height="10" viewBox="0 0 12 10"><path d="M2 1l4 4-4 4M6 1l4 4-4 4" fill="none" stroke="#fff" stroke-width="1.5"/></svg></div>

<!-- hours -->
<div class="photo" style="left:0;top:1742px;width:330px;height:531px;background:linear-gradient(180deg,#f2f2f2,#e9e9ea 70%,#c21d3a)" role="img" aria-label="Kok in witte jas die naar de openingsuren wijst"></div>
<div class="abs display" style="left:209px;top:1882px;font-size:29px;color:var(--blue)">VELKO EXPRESS</div>
<div class="abs hours">
  <b>Maandag</b> - 05:30-22:00<br>
  <b>Dinsdag</b> - 05:30-22:00<br>
  <b>Woensdag</b> - 05:30-22:00<br>
  <b>Donderdag</b> - 05:30-22:00<br>
  <b>Vrijdag</b>- 05:30-22:00<br>
  <b>Zaterdag</b> - 08:00-22:00<br>
  <b>Zondag</b>- 08:00-22:00
</div>
<div class="abs display" style="left:238px;top:2208px;font-size:23px;color:var(--navy)">Restaurant Van 08u</div>

<!-- contact form -->
<div class="abs form-box">
  <div class="abs display" style="left:25px;top:26px;font-size:31px">CONTACTEER ONS</div>
  <div class="abs" style="left:25px;top:80px;width:450px;font-size:12.5px;line-height:21.5px;font-weight:500">Heeft U Een Opmerking, Vraag Of Suggestie? Laat Het Ons Hier Weten. Reserveren Kan Enkel Telefonisch Via 011 720 310.</div>
  <div class="field" style="top:136px;height:39px">Email *</div>
  <div class="field" style="top:193px;height:38px">Naam *</div>
  <div class="field" style="top:249px;height:148px">Bericht *</div>
  <div class="btn btn-navy" style="left:24px;top:424px;width:118px;height:34px">Indienen</div>
</div>

<!-- blog -->
<div class="abs eyebrow" style="top:2320px">Updates Van Onze Blog</div>
<div class="abs section-title display" style="top:2350px">NIEUWS</div>
<div class="abs" style="left:215px;top:2404px;width:770px;text-align:center;font-size:12px;line-height:21.8px">It Is A Long Established Fact That A Reader Will Be Distracted By The Readable Content Of A Page When Looking At Its Layout. The Point Of Using Lorem Ipsum Is That It Has A More-Or-Less Normal Distribution Of Letters, As Opposed To Using 'Content Here, Content Here', Making It Look Like Readable English.</div>

<article class="post" style="top:2503px">
  <div class="post-img" style="background:linear-gradient(135deg,#c0765a,#4fb2c6 55%,#8d4a3a)" role="img" aria-label="Jonge gasten op een terras met blauwe zetels"></div>
  <div class="date">6<br>Juni</div>
  <h3 class="post-title display" style="font-weight:400">Lorem Ipsum Is Simply Dummy Text Of The Printing</h3>
  <div class="meta">
    <span><svg width="14" height="12" viewBox="0 0 14 12"><path d="M7 11 1.5 5.5A3 3 0 0 1 7 2a3 3 0 0 1 5.5 3.5Z" fill="none" stroke="#1a73c0"/></svg>2 Likes</span>
    <span><svg width="14" height="12" viewBox="0 0 14 12"><rect x="1" y="1" width="12" height="8" fill="none" stroke="#1a73c0"/><path d="M4 9v2l3-2" fill="none" stroke="#1a73c0"/></svg>2 Comments</span>
    <span><svg width="13" height="13" viewBox="0 0 13 13"><circle cx="6.5" cy="4" r="3" fill="none" stroke="#1a73c0"/><path d="M1 12.5a5.5 4 0 0 1 11 0Z" fill="none" stroke="#1a73c0"/></svg>By Admin</span>
  </div>
  <p class="post-text">It Is A Long Established Fact That A Reader Will Be Distracted By The Readable Content Of A Page When Looking At Its Layout. The Point Of Using Lorem Ipsum Is That It Has A More-Or-Less Normal Distribution Of Letters, As Opposed To Using</p>
  <div class="btn btn-blue" style="left:533px;top:212px;width:118px;height:35px">Lees Verder</div>
</article>

<article class="post" style="top:2788px">
  <div class="post-img" style="background:linear-gradient(135deg,#6a5040,#b7a898 50%,#2e3340)" role="img" aria-label="Medewerkster aan de kassa in de winkel"></div>
  <div class="date">16<br>Juni</div>
  <h3 class="post-title display" style="font-weight:400">Lorem Ipsum Is Simply Dummy Text Of The Printing</h3>
  <div class="meta">
    <span><svg width="14" height="12" viewBox="0 0 14 12"><path d="M7 11 1.5 5.5A3 3 0 0 1 7 2a3 3 0 0 1 5.5 3.5Z" fill="none" stroke="#1a73c0"/></svg>2 Likes</span>
    <span><svg width="14" height="12" viewBox="0 0 14 12"><rect x="1" y="1" width="12" height="8" fill="none" stroke="#1a73c0"/><path d="M4 9v2l3-2" fill="none" stroke="#1a73c0"/></svg>2 Comments</span>
    <span><svg width="13" height="13" viewBox="0 0 13 13"><circle cx="6.5" cy="4" r="3" fill="none" stroke="#1a73c0"/><path d="M1 12.5a5.5 4 0 0 1 11 0Z" fill="none" stroke="#1a73c0"/></svg>By Admin</span>
  </div>
  <p class="post-text">It Is A Long Established Fact That A Reader Will Be Distracted By The Readable Content Of A Page When Looking At Its Layout. The Point Of Using Lorem Ipsum Is That It Has A More-Or-Less Normal Distribution Of Letters, As Opposed To Using</p>
  <div class="btn btn-blue" style="left:533px;top:212px;width:118px;height:35px">Lees Verder</div>
</article>

<div class="btn btn-blue" style="left:514px;top:3089px;width:171px;height:34px">Bekijk Alle Berichten</div>

<!-- map + footer -->
<div class="abs map" role="img" aria-label="Kaart van de omgeving met locatiemarkering"></div>
<div class="abs" style="left:492px;top:3208px;width:118px;height:36px;background:#fff;border-radius:4px;font-size:12px;font-weight:600;display:flex;align-items:center;justify-content:center">Roadhaven 41Ter</div>
<svg class="abs" style="left:542px;top:3254px" width="18" height="28" viewBox="0 0 18 28"><path d="M9 27C9 27 1 15 1 9a8 8 0 0 1 16 0c0 6-8 18-8 18Z" fill="#e31b37"/><circle cx="9" cy="9" r="3" fill="#8a0f20"/></svg>
<div class="abs footer">
  <span class="abs dot-icon" style="left:56px;top:9px;background:#fff;opacity:.9"></span>
  <span class="abs dot-icon" style="left:88px;top:9px;background:#fff;opacity:.9"></span>
  <span class="abs" style="left:0;width:1200px;top:12px;text-align:center">Roadhaven 41Ter Staat Altijd Open Om Nieuwe Talenten Te Ontdekken.</span>
  <span class="abs" style="left:1056px;top:12px;font-weight:500">Privacy&nbsp;&nbsp;&nbsp;&nbsp;Policy</span>
</div>

</body>
</html>
```